Sale PPC Banner Ad Design Update

We need some Google PPC Banner Ad's for our sale altered to include product shots in the background. Attached are some examples that we currently use. We want a similar format/look but with the attached product shots used as the background image. Product image is called "KTPOle Grade 4"

Have also included our logo file as well.

Industry/Entity Type

Google

Font styles to use
Sans Serif

Requirements
Must have
• The must-have sizes (up to 150kb):
• • Banner: 468 x 60
• • Large mobile banner 320 x 100
• • Leaderboard: 728 x 90
• • Square: 250 x 250
• • Small square: 200 x 200
• • Large rectangle: 336 x 280
Nice to have
• The nice-to-have sizes:
• • Vertical rectangle: 240 x 400
• • Mobile leaderboard: 320 x 50
• • Inline rectangle: 300 x 250
• • Skyscraper: 120 x 600
• • Wide skyscraper: 160 x 600
• • Half-page: 300 x 600
• • Large leaderboard: 970 x 90
• • Billboard: 970 x 250
• • Portrait: 300 x 1050

```html
<!DOCTYPE html>
<html lang="en">
<head>
<meta charset="utf-8">
<title>KTPOle Luxury Shoes Sale – Portrait Banner</title>
<link rel="stylesheet" href="https://fonts.googleapis.com/css2?family=Montserrat:wght@400;500&display=swap">
<style>
  :root {
    --paper: #ffffff;
    --ink: #111111;
    --sale-red: #ea3a46;
    --headline-white: #f4f4f4;
    --photo-navy: #2b3566;
    --photo-deep-navy: #1c2244;
    --photo-red: #9a2436;
    --photo-maroon: #5e1a2c;
    --photo-gold: #8a7a22;
    --photo-leather: #2a2224;
    --photo-grey: #6d6d72;
    --photo-shade: rgba(0, 0, 0, 0.28);
  }
  * { margin: 0; padding: 0; box-sizing: border-box; }
  html, body {
    width: 1200px;
    height: 4200px;
    overflow: hidden;
    background: var(--paper);
  }
  .banner {
    position: relative;
    width: 1200px;
    height: 4200px;
    font-family: "Montserrat", Arial, sans-serif;
  }
  .brand-bar {
    position: absolute;
    left: 0;
    top: 0;
    width: 1200px;
    height: 608px;
    background: var(--paper);
    display: flex;
    align-items: center;
    justify-content: center;
  }
  .brand-name {
    font-weight: 400;
    font-size: 250px;
    letter-spacing: -6px;
    color: var(--ink);
    line-height: 1;
    margin-top: -30px;
  }
  .product-photo {
    position: absolute;
    left: 0;
    top: 608px;
    width: 1200px;
    height: 3592px;
    background:
      linear-gradient(var(--photo-shade), var(--photo-shade)),
      radial-gradient(ellipse 420px 700px at 330px 350px, var(--photo-navy) 0%, transparent 100%),
      radial-gradient(ellipse 520px 420px at 780px 1200px, var(--photo-grey) 0%, transparent 100%),
      radial-gradient(ellipse 460px 380px at 300px 1700px, var(--photo-leather) 0%, transparent 100%),
      radial-gradient(ellipse 520px 420px at 1000px 800px, var(--photo-gold) 0%, transparent 100%),
      radial-gradient(ellipse 420px 800px at 180px 2400px, var(--photo-navy) 0%, transparent 100%),
      radial-gradient(ellipse 560px 460px at 980px 2300px, var(--photo-red) 0%, transparent 100%),
      radial-gradient(ellipse 520px 420px at 820px 3250px, var(--photo-grey) 0%, transparent 100%),
      radial-gradient(ellipse 500px 420px at 300px 3300px, var(--photo-leather) 0%, transparent 100%),
      radial-gradient(ellipse 520px 460px at 1050px 3000px, var(--photo-gold) 0%, transparent 100%),
      linear-gradient(165deg, var(--photo-deep-navy) 0%, var(--photo-maroon) 30%, var(--photo-red) 50%, var(--photo-maroon) 70%, var(--photo-deep-navy) 100%);
  }
  .eyebrow,
  .sale-word,
  .call-to-action {
    position: absolute;
    left: 0;
    width: 1200px;
    text-align: center;
    line-height: 1;
  }
  .eyebrow {
    top: 2180px;
    font-weight: 500;
    font-size: 88px;
    letter-spacing: 20px;
    padding-left: 20px;
    color: var(--headline-white);
  }
  .sale-word {
    top: 2300px;
    font-weight: 400;
    font-size: 330px;
    letter-spacing: 30px;
    padding-left: 30px;
    color: var(--sale-red);
  }
  .call-to-action {
    top: 2635px;
    font-weight: 500;
    font-size: 88px;
    letter-spacing: 24px;
    padding-left: 24px;
    color: var(--headline-white);
  }
</style>
</head>
<body>
  <main class="banner">
    <header class="brand-bar">
      <span class="brand-name">KTPOle</span>
    </header>
    <div class="product-photo" role="img" aria-label="Product shot of KTPOle Grade 4 two-tone black and grey penny loafers worn with dotted navy trousers on a red, yellow and blue geometric rug"></div>
    <p class="eyebrow">LUXURY SHOES</p>
    <p class="sale-word">SALE</p>
    <p class="call-to-action">SHOP NOW</p>
  </main>
</body>
</html>
```